Modern Business Card

Modern professional business card with more than just logo and demographic info. Something memorable.

We are a trendy/modern chiropractic group with an emphasis on neurology, hence the minimalist-type brain logo. We want to convey that modern and technical aspect with professionalism and the elite nature of our practice environment.

```html
<!DOCTYPE html>
<html lang="en">
<head>
<meta charset="utf-8">
<title>Clarity Spine Care – Business Card</title>
<link rel="stylesheet" href="https://fonts.googleapis.com/css2?family=Cinzel:wght@500&family=Montserrat:wght@400&display=swap">
<style>
  :root {
    --page-bg: #d9d4cc;
    --card-light: #e4e2de;
    --panel-dark: #2b2a29;
    --brand-blue: #3a6e9c;
    --accent-blue: #2f6aa3;
    --arc-light: #cfc9bf;
    --text-light: #e6e3de;
    --text-muted: #c9c5be;
  }
  * { margin: 0; padding: 0; box-sizing: border-box; }
  html, body {
    width: 1200px;
    height: 1047px;
    overflow: hidden;
    background: var(--page-bg);
  }
  .card {
    position: absolute;
    left: 100px;
    top: 243px;
    width: 1000px;
    height: 560px;
    border-radius: 22px;
    overflow: hidden;
    background: var(--card-light);
    box-shadow: 0 10px 30px rgba(0,0,0,0.18);
  }
  .card-art {
    position: absolute;
    inset: 0;
  }
  .brand {
    position: absolute;
    left: 60px;
    top: 62px;
    font-family: "Cinzel", serif;
    font-weight: 500;
    color: var(--text-light);
    line-height: 1;
    display: flex;
    align-items: center;
    gap: 16px;
  }
  .brand-dot {
    width: 40px;
    height: 40px;
    border-radius: 50%;
    background: var(--brand-blue);
    flex: none;
  }
  .brand-name { font-size: 40px; letter-spacing: 1px; }
  .brand-sub { font-size: 22px; letter-spacing: 1.5px; margin-top: 6px; }
  .contact {
    position: absolute;
    left: 60px;
    top: 236px;
    font-family: "Montserrat", sans-serif;
    color: var(--text-muted);
  }
  .person-name {
    font-family: "Cinzel", serif;
    font-weight: 500;
    font-size: 30px;
    color: var(--brand-blue);
    letter-spacing: 1px;
  }
  .person-role { font-size: 23px; margin-top: 6px; }
  .address { font-size: 23px; line-height: 38px; margin-top: 20px; }
  .lines { list-style: none; margin-top: 16px; font-size: 23px; }
  .lines li { display: flex; align-items: center; gap: 14px; height: 34px; }
  .lines svg { width: 20px; height: 20px; flex: none; }
  .big-mark {
    position: absolute;
    left: 800px;
    top: 280px;
    transform: translate(-50%, -50%);
    text-align: center;
    font-family: "Cinzel", serif;
    font-weight: 500;
    color: var(--accent-blue);
    line-height: 1.1;
  }
  .big-mark .big-dot {
    width: 130px;
    height: 130px;
    border-radius: 50%;
    background: var(--accent-blue);
    margin: 0 auto 18px;
  }
  .big-mark .big-name { font-size: 44px; letter-spacing: 2px; }
</style>
</head>
<body>
  <div class="card">
    <svg class="card-art" viewBox="0 0 1000 560" width="1000" height="560" aria-hidden="true">
      <path d="M0,0 H645 A320,320 0 0 0 645,560 H0 Z" fill="var(--panel-dark)"/>
      <path d="M640,0 A325,325 0 0 0 640,560" fill="none" stroke="var(--arc-light)" stroke-width="8"/>
      <path d="M728,0 A400,400 0 0 0 728,560" fill="none" stroke="var(--accent-blue)" stroke-width="5" opacity="0"/>
      <path d="M672,2 A318,318 0 0 0 672,558" fill="none" stroke="var(--accent-blue)" stroke-width="6"/>
    </svg>

    <div class="brand">
      <span class="brand-dot"></span>
      <div>
        <div class="brand-name">CLARITY</div>
        <div class="brand-sub">SPINE CARE</div>
      </div>
    </div>

    <div class="contact">
      <div class="person-name">DANIEL MERCER</div>
      <div class="person-role">Director</div>
      <div class="address">1187 Birchwood Lane<br>Salem, OR 97301</div>
      <ul class="lines">
        <li>
          <svg viewBox="0 0 24 24"><path d="M6.6 3.5l3 3.2-1.8 2.3a13 13 0 0 0 7.2 7.2l2.3-1.8 3.2 3-2.2 3C10 19.8 4.2 14 3.6 5.7z" fill="none" stroke="var(--brand-blue)" stroke-width="1.8"/></svg>
          (555) 218-4470
        </li>
        <li>
          <svg viewBox="0 0 24 24"><rect x="3" y="6" width="18" height="12" fill="none" stroke="var(--brand-blue)" stroke-width="1.8"/><path d="M3 6l9 7 9-7" fill="none" stroke="var(--brand-blue)" stroke-width="1.8"/></svg>
          hello@clarityspine.com
        </li>
        <li>
          <svg viewBox="0 0 24 24"><circle cx="12" cy="12" r="9" fill="none" stroke="var(--brand-blue)" stroke-width="1.8"/><path d="M3 12h18M12 3c3 3 3 15 0 18M12 3c-3 3-3 15 0 18" fill="none" stroke="var(--brand-blue)" stroke-width="1.5"/></svg>
          www.clarityspine.com
        </li>
      </ul>
    </div>

    <div class="big-mark">
      <div class="big-dot"></div>
      <div class="big-name">CLARITY</div>
    </div>
  </div>
</body>
</html>
```